Book Cover needed for Printed Book entitled "Mile Ten"

The Book's Title is "Mile Ten", the sub-title is "A Neighbor's Handbook for Calm Roadside Meetings with Patrols", and the author is "Desmond Rawle". The front cover may have just the Title, or it may have a combination of the Title, Sub-Title, and Author. We would like to see designs that presents a feeling of peace and cooperation between US Police Officers and Civilians. The cover can include photographs, illustrations, or just words. But the cover should make the viewer want to open the book for more information.

Target Market(s)

Young adults who live in US inner-cities between ages 18 to 30.

Font styles to use
Sans Serif

Colors

Designer to choose colors to be used in the design.

Requirements
Must have
• Most US Police Officers use the phrase "MILE TEN" to tell other officers that the situation is under control and no assistance is needed. And the book will teach Civilians how to safely conduct themselves during police encounters - which will end with the Cops calling in "MILE TEN" to the dispatcher. So, the front cover must have the phrase "MILE TEN" in big bold letters.
Nice to have
• We would like to see designs that present a feeling of peace and cooperation between US Police Officers and Civilians. Pictures and illustrations of people are acceptable but is not required.

```html
<!DOCTYPE html>
<html lang="en">
<head>
<meta charset="utf-8">
<title>Mile Ten — Book Cover</title>
<link rel="stylesheet" href="https://fonts.googleapis.com/css2?family=Anton&family=Archivo:wght@800&family=Cinzel:wght@500&display=swap">
<style>
  :root {
    --navy-deep: #0b1436;
    --navy: #1a2c78;
    --blue-glow: #3a5fd6;
    --night: #05070f;
    --gold-light: #fbf0c8;
    --gold-mid: #e3c98a;
    --gold-dark: #9c7a43;
    --white: #ffffff;
    --rule-blue: #4e7bff;
  }
  html, body {
    margin: 0;
    padding: 0;
    overflow: hidden;
    background: var(--night);
  }
  .cover {
    position: relative;
    width: 800px;
    height: 1200px;
    overflow: hidden;
    background: var(--night);
  }
  .cover-scene {
    position: absolute;
    inset: 0;
    width: 800px;
    height: 1200px;
  }
  .title {
    position: absolute;
    left: 0;
    top: 236px;
    width: 800px;
    display: flex;
    justify-content: center;
    align-items: center;
    font-family: "Anton", "Impact", sans-serif;
    line-height: 1;
    margin: 0;
    font-weight: 400;
  }
  .title span {
    background: linear-gradient(180deg, var(--gold-light) 0%, var(--gold-mid) 55%, var(--gold-dark) 100%);
    -webkit-background-clip: text;
    background-clip: text;
    color: transparent;
    filter: drop-shadow(0 3px 4px rgba(0,0,0,0.55));
  }
  .title-initial { font-size: 290px; }
  .title-small { font-size: 168px; }
  .title-word-gap { display: inline-block; width: 22px; }
  .subtitle {
    position: absolute;
    left: 0;
    top: 512px;
    width: 800px;
    margin: 0;
    text-align: center;
    font-family: "Archivo", "Arial Black", sans-serif;
    font-weight: 800;
    font-size: 36px;
    line-height: 58px;
    color: var(--white);
    text-shadow: 0 2px 4px rgba(0,0,0,0.6);
  }
  .subtitle-rule {
    position: absolute;
    left: 340px;
    top: 626px;
    width: 172px;
    height: 2px;
    background: var(--rule-blue);
  }
  .author {
    position: absolute;
    left: 0;
    top: 1068px;
    width: 800px;
    margin: 0;
    text-align: center;
    font-family: "Cinzel", "Times New Roman", serif;
    font-weight: 500;
    font-size: 33px;
    letter-spacing: 0.14em;
    color: var(--white);
  }
</style>
</head>
<body>
<main class="cover">
  <svg class="cover-scene" viewBox="0 0 800 1200" role="img" aria-label="Night city skyline in deep blue with a glowing tunnel of light and blurred police car lights on a dark street">
    <defs>
      <linearGradient id="sky" x1="0" y1="0" x2="0" y2="1">
        <stop offset="0" stop-color="#0b1436"/>
        <stop offset="0.35" stop-color="#1a2c78"/>
        <stop offset="0.62" stop-color="#101a44"/>
        <stop offset="0.85" stop-color="#05070f"/>
        <stop offset="1" stop-color="#030409"/>
      </linearGradient>
      <radialGradient id="glow" cx="0.5" cy="0.5" r="0.5">
        <stop offset="0" stop-color="#6f8fff" stop-opacity="0.75"/>
        <stop offset="1" stop-color="#3a5fd6" stop-opacity="0"/>
      </radialGradient>
      <radialGradient id="lights" cx="0.5" cy="0.5" r="0.5">
        <stop offset="0" stop-color="#ff3d7a" stop-opacity="0.6"/>
        <stop offset="1" stop-color="#ff3d7a" stop-opacity="0"/>
      </radialGradient>
    </defs>
    <rect width="800" height="1200" fill="url(#sky)"/>
    <rect x="300" y="84" width="366" height="760" fill="#2542a8" opacity="0.35"/>
    <ellipse cx="405" cy="300" rx="230" ry="240" fill="url(#glow)"/>
    <ellipse cx="360" cy="980" rx="190" ry="70" fill="url(#lights)"/>
  </svg>

  <h1 class="title" aria-label="Mile Ten">
    <span class="title-initial">M</span><span class="title-small">ILE</span><span class="title-word-gap"></span><span class="title-small">TEN</span>
  </h1>

  <p class="subtitle">A Neighbor's Handbook For<br>Calm Roadside Meetings<br>With Patrols</p>
  <div class="subtitle-rule"></div>

  <p class="author">DESMOND RAWLE</p>
</main>
</body>
</html>
```